I am looking to create a newly designed website for our national leadership conference which is entitled, "The Harbor of Momentum Leadership Summit". The Harbor of Momentum Leadership Summit is a national conference for student leaders that prepares them for career leadership success. The current website can be seen at www.harborofmomentumleadershipsummit.com.

My goal for the new site is to create a more updated, fresh, hip, and exciting look that appeals to the younger generation while also maintaining are professional appeal. The color should be black, white, and gold. We want there to be live videos played and places to insert pictures for the panels as well.

I look forward to seeing you the new creations.

Requirements
Must have
• Ability to play videos on the home page and throughout the website. Also, make sure that the website shows up clearly on an zTablet.
Nice to have
• Nice look

```html
<!DOCTYPE html>
<html lang="en">
<head>
<meta charset="utf-8">
<title>Harbor of Momentum Leadership Summit</title>
<link href="https://fonts.googleapis.com/css2?family=Lato:wght@400;700&family=Open+Sans:wght@400;600&display=swap" rel="stylesheet">
<style>
:root{
  --gold:#b89a4e;
  --gold-dark:#a88a40;
  --ink:#1e1e1e;
  --navy:#2a3444;
  --grey:#8a8a8a;
  --line:#d6d6d6;
  --white:#ffffff;
  --black:#0c0c0c;
}
*{margin:0;padding:0;box-sizing:border-box}
html,body{width:862px;height:1200px;overflow:hidden;background:var(--white)}
body{font-family:"Open Sans",Arial,sans-serif;color:var(--ink);position:relative}
.abs{position:absolute}

/* header */
.site-header{position:absolute;left:0;top:0;width:862px;height:94px;background:var(--white)}
.brand{left:70px;top:18px;width:150px;height:62px;display:flex;flex-direction:column;align-items:center;justify-content:flex-end}
.brand-dot{width:36px;height:36px;border-radius:50%;background:var(--gold);margin-bottom:6px}
.brand-name{font-family:"Open Sans",sans-serif;font-weight:600;font-size:11.5px;letter-spacing:1px;color:var(--ink);white-space:nowrap}
.social-top{left:590px;top:24px;display:flex;gap:10px}
.social-top span{width:9px;height:9px;border-radius:50%;background:#444}
.btn-top{left:686px;top:16px;width:105px;height:25px;background:var(--gold);color:var(--white);font-size:9px;display:flex;align-items:center;justify-content:center;letter-spacing:.3px}
.main-nav{left:275px;top:62px;display:flex;gap:0;font-size:8.5px;color:var(--ink)}
.main-nav a{text-decoration:none;color:inherit;margin-right:26px;display:flex;align-items:center}
.main-nav a:last-child{margin-right:0}
.main-nav .active{color:var(--gold)}
.main-nav .active::before{content:"";width:8px;height:8px;border-radius:50%;background:var(--gold);margin-right:5px}

/* hero */
.hero{left:0;top:94px;width:862px;height:422px;background:radial-gradient(ellipse at 70% 40%,#6a6a6a 0%,#3c3c3c 45%,#1c1c1c 100%)}
.hero-title{left:10px;top:98px;font-size:14px;color:#e8e8e8}
.hero-icons{right:14px;top:100px;display:flex;gap:14px}
.play{left:407px;top:279px}
.dots{left:413px;top:503px;display:flex;gap:5px}
.dots span{width:5px;height:5px;border-radius:50%;background:#ddd}
.dots span:first-child{background:var(--gold)}

/* band */
.band{left:0;top:516px;width:862px;height:129px;background:var(--gold);text-align:center}
.band p{position:absolute;left:70px;top:16px;width:722px;font-size:15px;line-height:19px;color:var(--white)}
.btn-dark{left:366px;top:85px;width:129px;height:30px;background:#2a2522;color:var(--white);font-size:11px;display:flex;align-items:center;justify-content:center}

/* partners */
.partner{top:700px;width:200px;text-align:center}
.partner .badge{margin:0 auto;background:#cfcfcf}
.partner h3{font-weight:400;font-size:11.5px;line-height:17px;color:#333;margin-top:10px;letter-spacing:.2px}
.divider{top:723px;width:1px;height:115px;background:var(--line)}

/* who we are */
.who-title{left:72px;top:910px;font-family:Lato,sans-serif;font-weight:700;font-size:23px;color:var(--navy)}
.who-sub{left:72px;top:947px;font-size:14.5px;line-height:15px;color:#333}
.who-list{left:72px;top:1002px;list-style:none;font-family:Lato,sans-serif;font-size:7.5px;color:var(--grey)}
.who-list li{margin-bottom:9px;display:flex;align-items:center}
.who-list li::before{content:"";width:4px;height:4px;border:1px solid #666;border-radius:50%;margin-right:6px}
.btn-more{left:72px;top:1068px;width:74px;height:23px;border:1px solid var(--line);font-size:8.5px;color:#333;display:flex;align-items:center;justify-content:center}
.video-thumb{left:484px;top:918px;width:307px;height:173px;border-radius:3px;background:linear-gradient(135deg,#5a3a3a 0%,#3a3236 45%,#26242a 100%);overflow:hidden}
.video-thumb .vt-title{position:absolute;left:4px;top:4px;font-size:5.5px;color:#eee}
.video-thumb .vt-caption{position:absolute;left:0;width:100%;bottom:5px;text-align:center;font-size:10px;font-weight:600;color:var(--white);padding-left:60px}

/* footer */
.site-footer{left:0;top:1142px;width:862px;height:58px;background:var(--black)}
.social-foot{left:64px;top:25px;display:flex;gap:14px}
.social-foot span{width:13px;height:13px;border-radius:50%;background:#bbb}
.copyright{right:76px;top:22px;font-size:10px;color:#ddd}
</style>
</head>
<body>

<header class="site-header">
  <div class="abs brand">
    <span class="brand-dot"></span>
    <span class="brand-name">HARBOR OF MOMENTUM</span>
  </div>
  <div class="abs social-top"><span></span><span></span><span></span><span></span></div>
  <div class="abs btn-top">REGISTER NOW</div>
  <nav class="abs main-nav">
    <a class="active">HOME</a><a>ABOUT</a><a>CONFERENCE</a><a>REGISTER</a><a>TESTIMONIALS</a><a>Y FACTOR</a><a>VIDEOS</a><a>CONTACT</a>
  </nav>
</header>

<section class="abs hero" role="img" aria-label="Video still of a speaker handing a microphone to a student at the summit"></section>
<div class="abs hero-title">Attend the 2015 Harbor of Momentum Leadership Experience!</div>
<div class="abs hero-icons">
  <svg width="16" height="16" viewBox="0 0 16 16"><circle cx="8" cy="8" r="7.5" fill="#bbb"/><path d="M8 4v4.5l3 1.5" stroke="#333" stroke-width="1.4" fill="none"/></svg>
  <svg width="16" height="16" viewBox="0 0 16 16"><path d="M9 3l6 5-6 5v-3C5 10 3 11 1 14c1-5 4-8 8-8z" fill="#bbb"/></svg>
</div>
<svg class="abs play" width="46" height="46" viewBox="0 0 46 46"><circle cx="23" cy="23" r="21.5" fill="none" stroke="#fff" stroke-width="2.5"/><path d="M17 13l15 10-15 10z" fill="#fff"/></svg>
<div class="abs dots"><span></span><span></span><span></span><span></span></div>

<section class="abs band">
  <p>for a transformational leadership experience that will connect you with an incredible diverse leader-ship network of students and professionals that provide you with the inspiration and leadership/professional skills needed to take your life to the next level!</p>
  <div class="abs btn-dark">REGISTER NOW</div>
</section>

<div class="abs partner" style="left:74px">
  <div class="badge" style="width:120px;height:30px;margin-top:28px"></div>
  <h3>VOTED AS TOP STUDENT LEADER-<br>SHIP PROGRAM OF THE YEAR IN<br>2014</h3>
</div>
<div class="abs divider" style="left:318px"></div>
<div class="abs partner" style="left:339px">
  <div class="badge" style="width:80px;height:34px;margin-top:26px;background:#d8c9a6"></div>
  <h3>NETWORK WITH EXECUTIVES</h3>
</div>
<div class="abs divider" style="left:562px"></div>
<div class="abs partner" style="left:590px">
  <div class="badge" style="width:60px;height:60px;border-radius:50%;background:#2a3a5a"></div>
  <h3>CONNECT WITH OTHER STUDENT<br>LEADERS FROM</h3>
</div>

<h2 class="abs who-title">Who We Are?</h2>
<p class="abs who-sub">EXPERIENCE TRANSFORMATIONAL MOMENTS<br>LIKE THESE STUDENT LEADERS</p>
<ul class="abs who-list">
  <li>Cras commodo nisl eu eleifend blandit.</li>
  <li>Vestibulum vestibulum odio quis urna elementum, vel accumsan risus pretium.</li>
  <li>Suspendisse non sem id urna molestie pharetra ut in libero.</li>
</ul>
<div class="abs btn-more">View more&nbsp;›</div>

<div class="abs video-thumb" role="img" aria-label="Video still of a speaker addressing seated student leaders">
  <span class="vt-title">Attend the 2015 Harbor of Momentum Leadership Experience!</span>
  <svg class="abs" style="left:138px;top:71px" width="30" height="30" viewBox="0 0 30 30"><circle cx="15" cy="15" r="14" fill="rgba(0,0,0,.3)" stroke="#fff" stroke-width="1.5"/><path d="M11 8l10 7-10 7z" fill="#fff"/></svg>
  <span class="vt-caption">"You go to school to settle for something</span>
</div>

<footer class="abs site-footer">
  <div class="abs social-foot"><span></span><span></span><span></span><span></span></div>
  <div class="abs copyright">© yoursite - All Rights Reserved</div>
</footer>

</body>
</html>
```